Tovel & Associates - London New Letting and Property Management Company *

Tovel & Associates LTD is a new company based in London, and works with brand new residential property in the city centre.

We are aiming to have 1000 new properties a year.

We are looking for something modern and minimalistic :
Logo ,Monogram, Paper Head and Business Card.

Target Market(s)

Internation landlords

Industry/Entity Type

Real Estate

Logo Text

Tovel & Associates

Colors

Designer to choose colors to be used in the design.

Requirements
Nice to have
• A particular monogram with "TA"
Should not have
• Little House over the logo

```html
<!DOCTYPE html>
<html lang="en">
<head>
<meta charset="utf-8">
<title>Tovel &amp; Associates – Stationery</title>
<link href="https://fonts.googleapis.com/css2?family=Work+Sans:wght@400;500;600&display=swap" rel="stylesheet">
<style>
  :root {
    --bg: #dadada;
    --paper: #f2f2f2;
    --navy: #1b5075;
    --blue: #29abe2;
    --ink: #6b6b6b;
    --ink-dark: #555;
    --white: #ffffff;
  }
  * { margin: 0; padding: 0; box-sizing: border-box; }
  html, body { width: 1200px; height: 1062px; overflow: hidden; }
  body {
    position: relative;
    background: var(--bg);
    font-family: "Work Sans", Arial, sans-serif;
    color: var(--ink);
  }

  /* Wordmark */
  .wordmark { position: absolute; display: flex; align-items: center; }
  .wordmark__square { background: var(--blue); flex: none; }
  .wordmark__name {
    color: var(--navy);
    font-weight: 600;
    text-transform: uppercase;
    letter-spacing: 0.06em;
    line-height: 1.05;
    white-space: nowrap;
  }
  .wordmark--on-dark .wordmark__name { color: var(--white); }

  /* Letterhead */
  .letterhead {
    position: absolute; left: 100px; top: 94px;
    width: 620px; height: 876px;
    background: var(--paper);
    box-shadow: 0 2px 6px rgba(0,0,0,0.12);
  }
  .letterhead .wordmark { left: 40px; top: 26px; }
  .letterhead .wordmark__square { width: 28px; height: 28px; margin-right: 14px; }
  .letterhead .wordmark__name { font-size: 19px; }
  .letter__salutation {
    position: absolute; left: 40px; top: 188px;
    font-size: 17px; color: var(--ink-dark);
  }
  .letter__body { position: absolute; left: 40px; top: 242px; width: 540px; }
  .letter__body p {
    font-size: 12px; line-height: 16.4px; color: var(--ink);
    letter-spacing: -0.01em;
    position: absolute; left: 0; width: 540px;
  }
  .letter__closing { position: absolute; left: 40px; top: 628px; font-size: 15px; color: var(--ink-dark); }
  .letter__signature {
    position: absolute; left: 40px; top: 656px; width: 112px; height: 18px;
    background: linear-gradient(90deg, #cfcfcf, #e4e4e4);
    border-radius: 3px;
  }
  .letter__name { position: absolute; left: 40px; top: 688px; font-size: 14px; color: var(--ink-dark); }
  .letter__title { position: absolute; left: 40px; top: 706px; font-size: 11.5px; color: var(--ink-dark); }
  .letter__company {
    position: absolute; left: 40px; top: 722px;
    font-size: 8px; font-weight: 600; text-transform: uppercase; color: var(--ink-dark);
  }
  .rule { position: absolute; height: 2px; background: var(--navy); }
  .letterhead .rule { left: 40px; top: 779px; width: 540px; }

  .contact { position: absolute; list-style: none; }
  .contact li { display: flex; align-items: center; }
  .contact svg { flex: none; }
  .contact strong { color: var(--navy); font-weight: 500; }
  .letterhead .contact { left: 40px; top: 810px; font-size: 11.5px; line-height: 15px; }
  .letterhead .contact svg { width: 7px; height: 7px; margin-right: 5px; }
  .address { position: absolute; text-align: right; }
  .letterhead .address { right: 40px; top: 825px; font-size: 11.5px; line-height: 15px; }

  /* Standalone wordmark */
  .brand-display { left: 796px; top: 246px; }
  .brand-display .wordmark__square { width: 52px; height: 52px; margin-right: 22px; }
  .brand-display .wordmark__name { font-size: 27px; }

  /* Business cards */
  .card {
    position: absolute; width: 374px; height: 213px;
    box-shadow: 0 2px 6px rgba(0,0,0,0.12);
  }
  .card--front { left: 752px; top: 475px; background: var(--paper); }
  .card--front .wordmark { left: 18px; top: 22px; }
  .card--front .wordmark__square { width: 14px; height: 14px; margin-right: 8px; }
  .card--front .wordmark__name { font-size: 10px; }
  .card__name {
    position: absolute; right: 19px; top: 106px;
    font-size: 14.5px; font-weight: 500; color: var(--navy); text-transform: uppercase;
  }
  .card__role { position: absolute; right: 19px; top: 124px; font-size: 9.5px; }
  .card--front .rule { left: 18px; top: 143px; width: 337px; height: 1.5px; }
  .card--front .contact { left: 18px; top: 158px; font-size: 9.5px; line-height: 13px; }
  .card--front .contact svg { width: 5px; height: 5px; margin-right: 5px; }
  .card--front .address { right: 19px; top: 171px; font-size: 9.5px; line-height: 13px; }

  .card--back { left: 752px; top: 726px; background: var(--navy); }
  .card--back .wordmark { left: 94px; top: 80px; }
  .card--back .wordmark__square { width: 24px; height: 24px; margin-right: 14px; }
  .card--back .wordmark__name { font-size: 15px; }
</style>
</head>
<body>

<svg width="0" height="0" style="position:absolute">
  <defs>
    <symbol id="icon-phone" viewBox="0 0 10 10"><path d="M2 1h2l1 2-1.2 1a5 5 0 0 0 2.2 2.2L7 5l2 1v2c0 .6-.4 1-1 1A8 8 0 0 1 1 2c0-.6.4-1 1-1z" fill="#1b5075"/></symbol>
    <symbol id="icon-mail" viewBox="0 0 10 10"><rect x="0.5" y="2" width="9" height="6" fill="none" stroke="#1b5075"/><path d="M0.5 2l4.5 3.5L9.5 2" fill="none" stroke="#1b5075"/></symbol>
    <symbol id="icon-web" viewBox="0 0 10 10"><circle cx="5" cy="5" r="4.3" fill="#1b5075"/><path d="M0.7 5h8.6M5 .7c2 2.5 2 6.1 0 8.6M5 .7c-2 2.5-2 6.1 0 8.6" stroke="#f2f2f2" stroke-width="0.7" fill="none"/></symbol>
  </defs>
</svg>

<section class="letterhead">
  <div class="wordmark">
    <span class="wordmark__square"></span>
    <span class="wordmark__name">Tovel &amp;<br>Associates<br>LTD</span>
  </div>

  <p class="letter__salutation">Dear Sir</p>

  <div class="letter__body">
    <p style="top:0">Lorem ipsum dolor sit amet, an vel recteque dissentiet, detracto albucius platonem ex vel, eros repudiandae cu. Atqui aliquando nec an, unum graece adolescens vel ad. Id odio scae has, iudico euismod atomorum ius ea, cum ea honestatis quaerendum theophrastus. Mea honestatis quaerendum theophrastus. Mea</p>
    <p style="top:84px">Lorem ipsum dolor sit amet, an vel recteque dissentiet, detracto albucius platonem ex vel, eros repudiandae cu. Atqui aliquando nec an, unum graece adolescens vel ad. Id odio scae has, iudico euismod atomorum ius ea, cum ea honestatis quaerendum theophrastus. Mea doming repudiandae ex, cu cum civibus assentior posidonium. Quo etiam pertinax ex, te eros repudiandae cu. Atqui aliquando nec an, unum graece adolescens vel ad. Id odio scae honestatis quaerendum theophrastus. Mea</p>
    <p style="top:202px">Lorem ipsum dolor sit amet, an vel recteque dissentiet, detracto albucius platonem ex vel, eros repudiandae cu. Atqui aliquando nec an, unum graece adolescens vel ad. Id odio scae has, iudico euismod atomorum ius ea, cum ea honestatis quaerendum theophrastus. Mea honestatis quaerendum theophrastus. Mea</p>
    <p style="top:287px">Lorem ipsum dolor sit amet, an vel recteque dissentiet, detracto albucius platonem ex vel, eros repudiandae cu. Atqui aliquando nec an, unum graece adolescens vel ad. Id odio scae has, iudico euismod atomorum ius ea, cum ea honestatis quaerendum theophrastus. Mea honestatis quaerendum theophrastus. Mea</p>
  </div>

  <p class="letter__closing">Kind Regards</p>
  <div class="letter__signature" role="img" aria-label="Handwritten signature of Henry Caldwell"></div>
  <p class="letter__name">Henry Caldwell</p>
  <p class="letter__title">Chief Alchemist</p>
  <p class="letter__company">Harwick Estate Services Ltd</p>

  <div class="rule"></div>

  <ul class="contact">
    <li><svg><use href="#icon-phone"/></svg>+44 20 7946 0321</li>
    <li><svg><use href="#icon-mail"/></svg>info@tovelassociates.com</li>
    <li><svg><use href="#icon-web"/></svg>www.<strong>tovelassociates</strong>.com</li>
  </ul>
  <p class="address">14 Carlow Street<br>London NW1 7LH</p>
</section>

<div class="wordmark brand-display">
  <span class="wordmark__square"></span>
  <span class="wordmark__name">Tovel &amp;<br>Associates<br>LTD</span>
</div>

<section class="card card--front">
  <div class="wordmark">
    <span class="wordmark__square"></span>
    <span class="wordmark__name">Tovel &amp;<br>Associates<br>LTD</span>
  </div>
  <p class="card__name">Daniel Reeve</p>
  <p class="card__role">Director</p>
  <div class="rule"></div>
  <ul class="contact">
    <li><svg><use href="#icon-phone"/></svg>+44 20 7946 0321</li>
    <li><svg><use href="#icon-mail"/></svg>info@tovelassociates.com</li>
    <li><svg><use href="#icon-web"/></svg>www.<strong>tovelassociates</strong>.com</li>
  </ul>
  <p class="address">14 Carlow Street<br>London NW1 7LH</p>
</section>

<section class="card card--back">
  <div class="wordmark wordmark--on-dark">
    <span class="wordmark__square"></span>
    <span class="wordmark__name">Tovel &amp;<br>Associates<br>LTD</span>
  </div>
</section>

</body>
</html>
```